Business Card Design

We are a law firm which provides services to creditors.....we do collection litigation. I am wide open on suggestions. I was thinking of a square card? Alternatively, a vertically oriented standard card or a folded card.....something unique. I would like to use my firm logo and beyond that, I am open for any and all suggestions. I'm uncertain if the complete log is uploaded? If not, please let me email it to you.

Industry/Entity Type

Law Firm

Contact Information for Business Card

Hart, Crane & Dobbs, P.C.
Tom Dobbs, Lawyer
4387 N Larkspur Ave
Oklahoma City, OK 73924
tdobbs@HcdCounsel.com
www.HcdCounsel.com
mobile: 405-382-7914

```html
<!DOCTYPE html>
<html lang="en">
<head>
<meta charset="utf-8">
<title>Hart, Crane &amp; Dobbs, P.C. — Business Card</title>
<link rel="stylesheet" href="https://fonts.googleapis.com/css2?family=Arimo:wght@400;700&display=swap">
<style>
  :root {
    --backdrop: #2b2b2d;
    --green-light: #0a7d45;
    --green-mid: #06703b;
    --green-dark: #045a2e;
    --gold: #dcb55a;
    --gold-soft: #c9a24a;
  }
  * { margin: 0; padding: 0; box-sizing: border-box; }
  html, body {
    width: 1200px; height: 922px; overflow: hidden;
    background: var(--backdrop);
    font-family: "Arimo", Arial, sans-serif;
  }
  .sheet {
    width: 1200px; height: 922px;
    display: flex; flex-direction: column;
    align-items: center; justify-content: center; gap: 40px;
  }
  .card {
    position: relative;
    width: 700px; height: 400px;
    border-radius: 22px;
    background: radial-gradient(ellipse at 60% 20%, var(--green-light) 0%, var(--green-mid) 45%, var(--green-dark) 100%);
    color: var(--gold);
    box-shadow: 0 10px 30px rgba(0,0,0,0.45);
  }
  .firm-mark {
    display: flex; align-items: center; gap: 12px;
    font-weight: 700; color: var(--gold);
  }
  .firm-mark .dot {
    border-radius: 50%;
    background: var(--gold);
    flex: none;
  }

  /* front */
  .card-front .firm-mark {
    position: absolute; left: 0; right: 0; top: 110px;
    justify-content: center; font-size: 30px;
  }
  .card-front .firm-mark .dot { width: 64px; height: 64px; }
  .card-front .firm-name {
    position: absolute; left: 0; right: 0; top: 240px;
    text-align: center; font-size: 50px; font-weight: 700;
  }

  /* back */
  .card-back .firm-mark {
    position: absolute; left: 48px; top: 48px; font-size: 20px;
  }
  .card-back .firm-mark .dot { width: 44px; height: 44px; }
  .card-back .firm-name {
    position: absolute; right: 40px; top: 120px;
    font-size: 36px; font-weight: 700;
  }
  .contact {
    position: absolute; left: 60px; top: 210px;
    list-style: none; font-size: 19px; line-height: 1.45;
  }
  .divider {
    position: absolute; left: 440px; top: 220px;
    width: 2px; height: 150px; background: var(--gold-soft);
  }
  .person {
    position: absolute; left: 480px; top: 270px;
  }
  .person-name { font-size: 44px; font-weight: 400; line-height: 1; }
  .person-role { font-size: 16px; margin-top: 4px; }
</style>
</head>
<body>
<main class="sheet">
  <section class="card card-front" aria-label="Card front">
    <div class="firm-mark"><span class="dot"></span>Hart, Crane &amp; Dobbs</div>
    <h1 class="firm-name">Hart, Crane &amp; Dobbs</h1>
  </section>

  <section class="card card-back" aria-label="Card back">
    <div class="firm-mark"><span class="dot"></span>Hart, Crane &amp; Dobbs</div>
    <h2 class="firm-name">Hart, Crane &amp; Dobbs, P.C.</h2>
    <ul class="contact">
      <li>405-382-7914</li>
      <li>www.HcdCounsel.com</li>
      <li>tdobbs@HcdCounsel.com</li>
      <li>4387 N Larkspur Ave Oklahoma City,<br>OK 73924</li>
    </ul>
    <div class="divider"></div>
    <div class="person">
      <p class="person-name">Tom Dobbs</p>
      <p class="person-role">Lawyer</p>
    </div>
  </section>
</main>
</body>
</html>
```